eBook-Cover für Thriller gesucht
An dieser Stelle ein großes Lob und vielen Dank an die Designerin Larosa. Auch das zweite Buchcover ist wieder überaus gelungen, eine ganz tolle Arbeit. Auch die angenehme Zusammenarbeit war mir, wie schon beim ersten Auftrag, eine Freude. Ebenso hervorzuheben ist die Schnelligkeit und Kreativität, mit der die Designerin auf Änderungswünsche reagiert. Als Auftraggeber gebe ich verdiente fünf Sterne und bin mit dem Ergebnis wirklich sehr zufrieden.
Zielgruppe
Ich bin Autor. Zielgruppe sind (anspruchsvolle) Leser/innen von Thrillern und Kriminalromanen im ebook-Bereich.
Aufgabenstellung
- Gesucht wird ein ebook-Cover für einen Thriller mit dem Titel 'Kaltgrund'
- Grobe Aufteilung siehe Skizzen
- Fokus des Covers liegt auf dem Buchtitel und dem Motiv ('Blauer Drachen')
- Hintergrund eher hell, Assoziation mit zarter Eisfläche mit angedeuteten Rissen vom Hauptmotiv ausgehend. Dadurch auch Tiefe und Dreidimensionalität. (Beispiel zum Hintergrund: 'Schattenfrist' von Heinrich Wendel, jedoch ohne Blut )
-Titelschrift groß, Stil 'gekratzt' bzw. 'gestrichelt', (Schriftart ähnlich wie Autorenname bei 'Die Schleuse' von Matthias Kolbe). Schrift groß und 'treppenförmig' neben dem Hauptmotiv angeordnet. Schriftfarbe schwarz/dunkelblau, ähnlich Hauptmotiv (Bsp.: 'Schwarzeid' von Heinrich Wendel)
Hauptmotiv ist der vom rechten Coverrand hineinragende 'Blaue Drachen' (Glaucus atlanticus, siehe hochgeladenes Beispielbild von Wissnetz)
- Schriftart von Autorenname und Genre eher klar
- eigene Detailvorschläge zur Optimierung des Ergebnisses möglich bzw. erwünscht

```html
<!DOCTYPE html>
<html lang="de">
<head>
<meta charset="utf-8">
<title>Kaltgrund – Thriller</title>
<link rel="stylesheet" href="https://fonts.googleapis.com/css2?family=Josefin+Sans:wght@400;600&family=Rubik+Dirt&display=swap">
<style>
  :root {
    --ice-white: #fbfdfe;
    --ice-pale: #dcedf3;
    --ice-blue: #a9d0df;
    --ice-deep: #6eaac3;
    --dragon-dark: #1d2748;
    --dragon-mid: #34477a;
    --ink: #141414;
  }
  * { margin: 0; padding: 0; box-sizing: border-box; }
  html, body {
    width: 811px; height: 1200px; overflow: hidden;
    background: var(--ice-white);
  }
  .cover {
    position: relative;
    width: 811px; height: 1200px;
    overflow: hidden;
    background: var(--ice-white);
  }
  .ice-surface, .dragon-motif {
    position: absolute;
    left: 0; top: 0;
    width: 811px; height: 1200px;
  }
  .author {
    position: absolute;
    left: 57px; top: 46px;
    font-family: "Josefin Sans", sans-serif;
    font-weight: 600;
    font-size: 31px;
    line-height: 1;
    letter-spacing: 0.3em;
    color: var(--ink);
    text-transform: uppercase;
  }
  .title-block { font-weight: normal; }
  .title {
    position: absolute;
    font-family: "Rubik Dirt", "Josefin Sans", sans-serif;
    font-weight: 400;
    font-size: 160px;
    line-height: 1;
    color: var(--ink);
    letter-spacing: 0.02em;
  }
  .title-line-1 { left: 60px;  top: 618px; }
  .title-line-2 { left: 204px; top: 770px; }
  .title-line-3 { left: 420px; top: 900px; }
  .genre {
    position: absolute;
    left: 522px; top: 1118px;
    font-family: "Josefin Sans", sans-serif;
    font-weight: 400;
    font-size: 29px;
    line-height: 1;
    letter-spacing: 0.4em;
    color: var(--ink);
  }
</style>
</head>
<body>
  <main class="cover">
    <svg class="ice-surface" viewBox="0 0 811 1200" role="img" aria-label="Helle, zarte Eisfläche mit feinen blauen Rissen, die vom Hauptmotiv ausgehen">
      <defs>
        <radialGradient id="iceCore" cx="0.72" cy="0.42" r="0.62">
          <stop offset="0" stop-color="var(--ice-deep)"/>
          <stop offset="0.35" stop-color="var(--ice-blue)"/>
          <stop offset="0.7" stop-color="var(--ice-pale)"/>
          <stop offset="1" stop-color="var(--ice-white)"/>
        </radialGradient>
      </defs>
      <rect width="811" height="1200" fill="url(#iceCore)"/>
    </svg>

    <svg class="dragon-motif" viewBox="0 0 811 1200" role="img" aria-label="Foto: Blauer Drachen (Glaucus atlanticus), ragt vom rechten Rand diagonal auf die Eisfläche">
      <defs>
        <radialGradient id="dragonTone" cx="0.5" cy="0.5" r="0.5">
          <stop offset="0" stop-color="var(--dragon-dark)" stop-opacity="0.85"/>
          <stop offset="0.55" stop-color="var(--dragon-mid)" stop-opacity="0.55"/>
          <stop offset="1" stop-color="var(--dragon-mid)" stop-opacity="0"/>
        </radialGradient>
      </defs>
      <ellipse cx="610" cy="380" rx="330" ry="260" transform="rotate(35 610 380)" fill="url(#dragonTone)"/>
    </svg>

    <p class="author">Lorenz Brandt</p>

    <h1 class="title-block" aria-label="Kaltgrund">
      <span class="title title-line-1" aria-hidden="true">KAL</span>
      <span class="title title-line-2" aria-hidden="true">TGR</span>
      <span class="title title-line-3" aria-hidden="true">UND</span>
    </h1>

    <p class="genre">THRILLER</p>
  </main>
</body>
</html>
```